Business Card for beauty technology startup

Design Glimora Business Card for a Beauty, based on the website identity and colors (https://www.glimora-example.com).
Glimora is a beauty tech startup that gathers helpful product info for beauty lovers and consumers (such as availability on stores, price range and product reviews) for makeup products. The card design must be young, colorful but clean, and very modern.

Target Market(s)

woman, 15-35

Industry/Entity Type

Cosmetics

Contact Information for Business Card

Full Name, address, phone

Font styles to use
Other font styles liked:
• Advent Pro

Colors
e34297
86cfc6
ffffff
5c5c5c
e8e8e8
e667a6
b2b2b2

Requirements
Must have
• One full colored side with a creative design and another with card info
• Use Color palette: #95C5C5 and/or #D38AA5
• Use fonts: Advent Pro
• Use website identity: https://www.glimora-example.com
Nice to have
• If needed extra font: Roboto

```html
<!DOCTYPE html>
<html lang="en">
<head>
<meta charset="utf-8">
<title>Glimora Business Card</title>
<link rel="stylesheet" href="https://fonts.googleapis.com/css2?family=Advent+Pro:wght@300;400&family=Montserrat:wght@400;600&display=swap">
<style>
  :root {
    --backdrop: #e8e8e8;
    --teal: #95c5c5;
    --white: #ffffff;
    --rose: #b4708f;
    --ink: #4a4a4a;
    --ghost: #f3f3f3;
  }
  * { margin: 0; padding: 0; box-sizing: border-box; }
  html, body { width: 1200px; height: 1155px; overflow: hidden; }
  body { background: var(--backdrop); position: relative; font-family: "Montserrat", sans-serif; }

  .card {
    position: absolute;
    left: 219px;
    width: 757px;
    height: 434px;
    border-radius: 32px;
    overflow: hidden;
    box-shadow: 4px 6px 10px rgba(0,0,0,0.18);
  }
  .card--front { top: 134px; background: var(--teal); }
  .card--back { top: 596px; background: var(--white); }

  .front-mark {
    position: absolute;
    left: 269px; top: 106px;
    width: 220px; height: 220px;
    border: 4px solid var(--white);
    border-radius: 50%;
    display: flex; align-items: center; justify-content: center;
  }
  .front-mark__name {
    font-family: "Advent Pro", sans-serif;
    font-weight: 400;
    font-size: 44px;
    letter-spacing: 3px;
    color: var(--white);
  }
  .social-row {
    position: absolute;
    left: 309px; top: 370px;
    display: flex; gap: 12px;
  }
  .social-row__dot {
    width: 29px; height: 29px;
    border-radius: 50%;
    background: var(--white);
  }

  .back-watermark { position: absolute; left: 322px; top: 0; }

  .brand {
    position: absolute;
    left: 391px; top: 44px;
    display: flex; align-items: center; gap: 18px;
  }
  .brand__circle {
    width: 76px; height: 76px;
    border: 2px solid var(--rose);
    border-radius: 50%;
  }
  .brand__name {
    font-family: "Advent Pro", sans-serif;
    font-weight: 300;
    font-size: 60px;
    letter-spacing: 5px;
    color: var(--rose);
    line-height: 1;
  }

  .contact {
    position: absolute;
    left: 43px; top: 190px;
    color: var(--ink);
  }
  .contact__name {
    font-weight: 600;
    font-size: 25px;
    color: var(--rose);
    line-height: 1;
  }
  .contact__role {
    font-size: 13px;
    letter-spacing: 0.5px;
    margin-top: 10px;
  }
  .contact__address {
    font-size: 19px;
    line-height: 28px;
    margin-top: 12px;
  }
  .contact__list { list-style: none; margin-top: 8px; }
  .contact__item {
    display: flex; align-items: center;
    font-size: 19px; line-height: 28px;
  }
  .contact__icon { width: 12px; height: 12px; margin-right: 16px; }
</style>
</head>
<body>

<section class="card card--front" aria-label="Card front">
  <div class="front-mark"><span class="front-mark__name">GLIMORA</span></div>
  <div class="social-row" aria-label="Social media links">
    <span class="social-row__dot"></span>
    <span class="social-row__dot"></span>
    <span class="social-row__dot"></span>
    <span class="social-row__dot"></span>
  </div>
</section>

<section class="card card--back" aria-label="Card back">
  <svg class="back-watermark" width="435" height="434" viewBox="0 0 435 434" aria-hidden="true">
    <circle cx="215" cy="216" r="212" fill="none" stroke="var(--ghost)" stroke-width="8"/>
  </svg>

  <div class="brand">
    <span class="brand__circle"></span>
    <span class="brand__name">GLIMORA</span>
  </div>

  <div class="contact">
    <p class="contact__name">DANA CORVELL</p>
    <p class="contact__role">OWNER</p>
    <p class="contact__address">27 Palm Row<br>Seabrook, FL 30012</p>
    <ul class="contact__list">
      <li class="contact__item">
        <svg class="contact__icon" viewBox="0 0 12 12" aria-hidden="true"><path d="M3 1 L5 3 L4 5 Q5 7 7 8 L9 7 L11 9 L10 11 Q4 11 1 3 Z" fill="var(--rose)"/></svg>
        555.014.2746
      </li>
      <li class="contact__item">
        <svg class="contact__icon" viewBox="0 0 12 12" aria-hidden="true"><rect x="1" y="3" width="10" height="7" fill="none" stroke="var(--rose)" stroke-width="1.2"/><path d="M1 3 L6 7 L11 3" fill="none" stroke="var(--rose)" stroke-width="1.2"/></svg>
        info@glimora-example.com
      </li>
      <li class="contact__item">
        <svg class="contact__icon" viewBox="0 0 12 12" aria-hidden="true"><circle cx="6" cy="6" r="5" fill="none" stroke="var(--rose)" stroke-width="1.2"/><path d="M1 6 H11 M6 1 Q3 6 6 11 M6 1 Q9 6 6 11" fill="none" stroke="var(--rose)" stroke-width="1"/></svg>
        www.glimora-example.com
      </li>
    </ul>
  </div>
</section>

</body>
</html>
```